Restyle corporate identity (+ logo) for a road construction company

We need a new logo and stationary design for our company VARNOK path. VARNOK path® increases the road base strength, while reducing major costs and time of road construction. Attached some examples of the current design.

Our wishes for the new logo:
- Business look
- Style sheet
- Modern

More information: www.varnokpath.example
Updates

Target Market(s)

Government

Industry/Entity Type

Construction

Requirements
Must have
• Logo (with road sign) + text

```html
<!DOCTYPE html>
<html lang="en">
<head>
<meta charset="utf-8">
<title>VARNOK path – Business Cards</title>
<link rel="stylesheet" href="https://fonts.googleapis.com/css2?family=Open+Sans:wght@400;500;600&display=swap">
<style>
  :root {
    --backdrop: #8e8f90;
    --card: #f2f3f5;
    --brand-blue: #1a82e2;
    --brand-grey: #8a8b8e;
    --text-dark: #4a4b4e;
    --text-muted: #8b8c8f;
    --watermark: #dde6f0;
  }
  * { box-sizing: border-box; margin: 0; padding: 0; }
  html, body {
    width: 1105px; height: 1200px; overflow: hidden;
    background: var(--backdrop);
    font-family: "Open Sans", Arial, sans-serif;
  }
  .canvas { position: relative; width: 1105px; height: 1200px; }
  .card {
    position: absolute; left: 182px; width: 746px; height: 425px;
    background: var(--card); overflow: hidden;
  }
  .card--front { top: 120px; }
  .card--back { top: 637px; }

  .name-marker { position: absolute; left: 0; top: 54px; width: 17px; height: 54px; background: var(--brand-blue); }
  .holder-name { position: absolute; left: 53px; top: 52px; font-size: 25px; font-weight: 600; color: var(--brand-blue); letter-spacing: 0.3px; }
  .holder-role { position: absolute; left: 53px; top: 84px; font-size: 19px; color: var(--text-muted); }

  .address { position: absolute; left: 53px; top: 190px; font-size: 19px; line-height: 26px; font-style: normal; color: var(--text-dark); }
  .contacts { position: absolute; left: 53px; top: 280px; list-style: none; font-size: 19px; line-height: 29px; color: var(--text-dark); }
  .contacts li { display: flex; align-items: center; gap: 10px; }
  .contacts svg { width: 18px; height: 18px; fill: var(--brand-blue); flex: none; }

  .wordmark {
    position: absolute; display: flex; align-items: center; gap: 12px;
    font-weight: 600; color: var(--brand-blue); white-space: nowrap;
  }
  .wordmark__square { background: var(--brand-blue); flex: none; }
  .card--front .wordmark { left: 412px; top: 272px; font-size: 36px; }
  .card--front .wordmark__square { width: 28px; height: 28px; }

  .band { position: absolute; bottom: 0; height: 23px; }
  .band--blue { left: 0; width: 515px; background: var(--brand-blue); }
  .band--grey { left: 519px; right: 0; background: var(--brand-grey); }

  .watermark-square { position: absolute; left: 35px; top: 31px; width: 370px; height: 370px; border-radius: 34px; background: var(--watermark); }
  .card--back .wordmark { right: 56px; top: 282px; font-size: 38px; }
  .back-url { position: absolute; right: 56px; top: 360px; font-size: 18px; color: var(--text-dark); letter-spacing: 1px; }
</style>
</head>
<body>
<div class="canvas">

  <section class="card card--front" aria-label="Business card front">
    <div class="name-marker"></div>
    <h1 class="holder-name">MAREN HOLT</h1>
    <p class="holder-role">CEO/Founder</p>

    <address class="address">
      Lindenkade 58<br>
      4811 TK Westerveld<br>
      The Netherlands
    </address>

    <ul class="contacts">
      <li>
        <svg viewBox="0 0 24 24" aria-hidden="true"><path d="M6.6 10.8a15.1 15.1 0 0 0 6.6 6.6l2.2-2.2a1 1 0 0 1 1-.25 11.4 11.4 0 0 0 3.6.57 1 1 0 0 1 1 1V20a1 1 0 0 1-1 1A17 17 0 0 1 3 4a1 1 0 0 1 1-1h3.5a1 1 0 0 1 1 1c0 1.25.2 2.45.57 3.57a1 1 0 0 1-.25 1z"/></svg>
        512 804 3967
      </li>
      <li>
        <svg viewBox="0 0 24 24" aria-hidden="true"><path d="M2 5h20v14H2zm2 2v.4l8 5 8-5V7zm0 2.8V17h16V9.8l-8 5z"/></svg>
        mail@varnokpath.example
      </li>
      <li>
        <svg viewBox="0 0 24 24" aria-hidden="true"><path d="M12 2a10 10 0 1 0 0 20 10 10 0 0 0 0-20zm6.9 6h-3a15 15 0 0 0-1.3-3.9A8 8 0 0 1 18.9 8zM12 4c.8 1.1 1.5 2.5 1.9 4h-3.8c.4-1.5 1.1-2.9 1.9-4zM4.3 14a8 8 0 0 1 0-4h3.4a16 16 0 0 0 0 4zm.8 2h3a15 15 0 0 0 1.3 3.9A8 8 0 0 1 5.1 16zm3-8h-3a8 8 0 0 1 4.3-3.9A15 15 0 0 0 8.1 8zM12 20c-.8-1.1-1.5-2.5-1.9-4h3.8c-.4 1.5-1.1 2.9-1.9 4zm2.3-6H9.7a14 14 0 0 1 0-4h4.6a14 14 0 0 1 0 4zm.3 5.9a15 15 0 0 0 1.3-3.9h3a8 8 0 0 1-4.3 3.9zm1.7-5.9a16 16 0 0 0 0-4h3.4a8 8 0 0 1 0 4z"/></svg>
        www.varnokpath.example
      </li>
    </ul>

    <div class="wordmark"><span class="wordmark__square"></span>VARNOK path</div>

    <div class="band band--blue"></div>
    <div class="band band--grey"></div>
  </section>

  <section class="card card--back" aria-label="Business card back">
    <div class="watermark-square"></div>
    <div class="wordmark">VARNOK path</div>
    <p class="back-url">www.varnokpath.example</p>
  </section>

</div>
</body>
</html>
```